Financial Services Flyer in English one side Spanish the other side

Hello - we are looking for good flyer that will be one side English, the other side exact same language in Spanish.... For the Flyer -

We show businesses how to save Thousands by Eliminating the percentage you are paying to accept Credit & Debit Cards... No more %!?? Yes, it's true!

We provide a free placed terminal or POS with a minimal monthly service fee.

On the Spanish Side; include "We specialize in Latina Businesses with Spanish Sales and Support staff"
We specialize in Latina Businesses with Spanish Sales and Support staff.
Nos especializamos en negocios latinos con personal de ventas y soporte en espaƱol.

Target Market(s)

Any business

Industry/Entity Type

any business that accepts credit cards.

Requirements
Must have
• WE need a white box on the flyers to place a label with the various agents name and contact.
Nice to have
• You can include pictures I uploaded, especially the logo and some equipment...

```html
<!DOCTYPE html>
<html lang="en">
<head>
<meta charset="utf-8">
<title>Keystone Payments – Flyers EN / ES</title>
<link href="https://fonts.googleapis.com/css2?family=Plus+Jakarta+Sans:wght@400;600;700;800&display=swap" rel="stylesheet">
<style>
  :root{
    --page:#e4e4e4;
    --navy:#060b1a;
    --navy-2:#0a1733;
    --blue:#1c6fd1;
    --blue-deep:#1048a0;
    --sky:#2a9df4;
    --yellow:#f3c316;
    --yellow-text:#f5cc1c;
    --ink:#0e1f5c;
    --white:#ffffff;
    --red:#e3241b;
  }
  *{box-sizing:border-box;margin:0;padding:0}
  html,body{width:1200px;height:870px;overflow:hidden;background:var(--page);
    font-family:"Plus Jakarta Sans",Arial,sans-serif}
  .sheet{position:relative;width:1200px;height:870px}

  .flyer{position:absolute;top:113px;width:499px;height:645px;overflow:hidden;color:var(--white);
    background:
      radial-gradient(ellipse 70% 55% at 100% 0%, var(--blue) 0%, rgba(28,111,209,.35) 45%, transparent 75%),
      linear-gradient(180deg,var(--navy) 0%,var(--navy-2) 100%);
    box-shadow:0 8px 14px rgba(0,0,0,.28)}
  .flyer--en{left:81px}
  .flyer--es{left:621px}

  .chart{position:absolute;left:0;top:330px;width:499px;height:180px;opacity:.5}

  .brand{position:absolute;left:30px;top:55px;display:flex;align-items:center;gap:9px}
  .brand__dot{width:30px;height:30px;border-radius:50%;background:var(--blue)}
  .brand__name{font-weight:700;font-size:24px;color:var(--sky);letter-spacing:.5px}

  .panel{position:absolute;left:308px;top:43px;width:167px;height:464px;
    background:var(--yellow);border-radius:84px 84px 0 0;
    box-shadow:6px -4px 0 0 var(--blue-deep)}
  .panel__kicker{position:absolute;left:330px;width:145px;font-size:8px;font-weight:600;color:var(--ink);white-space:nowrap}
  .panel__title{position:absolute;left:330px;width:142px;font-weight:800;color:var(--ink);letter-spacing:-.5px}
  .panel__sub{position:absolute;left:330px;width:115px;font-size:8.5px;line-height:1.3;color:var(--ink)}
  .panel__sub b{font-weight:700}

  .intro{position:absolute;left:30px;width:230px;font-size:11.5px;line-height:1.3}
  .intro em{font-style:normal;display:block;color:var(--yellow-text);font-weight:700}
  .headline{position:absolute;left:29px;font-weight:800;font-size:38px;line-height:1.05;letter-spacing:-1px;white-space:nowrap}
  .headline span{display:block;color:var(--yellow-text)}

  .pill{position:absolute;left:30px;top:279px;height:25px;padding:0 12px;border-radius:7px;
    background:var(--blue);display:flex;align-items:center;font-size:11.5px;font-weight:700;white-space:nowrap}
  .pill b{color:var(--yellow-text)}

  .offer__icon{position:absolute;left:32px;width:46px;height:46px;border-radius:50%;background:var(--yellow)}
  .offer__text{position:absolute;left:85px;width:140px;font-size:12px;line-height:1.22}
  .offer__text strong{color:var(--sky);font-weight:700}

  .photo{position:absolute;left:302px;top:240px;width:197px;height:267px;
    border-radius:70px 70px 0 0;
    background:linear-gradient(160deg,#e9d36a 0%,#c7a66a 40%,#2b3650 100%)}

  .seal{position:absolute;left:392px;top:218px;width:90px;height:90px;border-radius:50%;
    background:var(--red);text-align:center;color:var(--white);padding:17px 6px 0}
  .seal small{display:block;font-size:5.5px;font-weight:600;margin-bottom:5px}
  .seal p{font-size:7.5px;font-weight:700;line-height:1.15}

  .contact__tab{position:absolute;left:30px;top:487px;width:242px;height:20px;padding-left:10px;
    background:var(--blue);clip-path:polygon(0 0,94% 0,100% 100%,0 100%);
    border-radius:4px 0 0 0;font-size:8.5px;font-weight:700;line-height:20px;white-space:nowrap}
  .contact__box{position:absolute;left:30px;top:507px;width:436px;height:87px;background:var(--white);border-radius:6px}

  .site{position:absolute;left:0;right:0;top:603px;text-align:center;font-size:13px;font-weight:700;letter-spacing:5px;color:var(--sky)}
  .site span{color:var(--yellow-text)}
</style>
</head>
<body>
<main class="sheet">

  <!-- English side -->
  <article class="flyer flyer--en" lang="en">
    <svg class="chart" viewBox="0 0 499 180" aria-hidden="true">
      <g fill="#1e56b3">
        <rect x="20" y="110" width="6" height="70"/><rect x="40" y="90" width="6" height="90"/>
        <rect x="60" y="120" width="6" height="60"/><rect x="80" y="70" width="6" height="110"/>
        <rect x="100" y="100" width="6" height="80"/><rect x="120" y="60" width="6" height="120"/>
        <rect x="140" y="85" width="6" height="95"/><rect x="160" y="50" width="6" height="130"/>
        <rect x="180" y="95" width="6" height="85"/><rect x="200" y="40" width="6" height="140"/>
        <rect x="220" y="75" width="6" height="105"/><rect x="240" y="55" width="6" height="125"/>
        <rect x="260" y="80" width="6" height="100"/><rect x="280" y="45" width="6" height="135"/>
      </g>
      <polyline points="10,130 60,100 110,115 160,70 210,85 260,40 300,30" fill="none" stroke="#2a9df4" stroke-width="1.5"/>
    </svg>

    <div class="brand"><span class="brand__dot"></span><span class="brand__name">KEYSTONE</span></div>

    <div class="panel"></div>
    <p class="panel__kicker" style="top:105px">Keystone Payments take the</p>
    <h2 class="panel__title" style="top:116px;font-size:20px;line-height:1.05">PAIN out of Payment Processing</h2>
    <p class="panel__sub" style="top:192px">By <b>delivering more of your profit to you!</b></p>

    <div class="photo" role="img" aria-label="Smiling shopper holding a card and shopping bags beside a card terminal and a bag of cash"></div>

    <p class="intro" style="top:140px">How to save Thousands by<em>Eliminating the percentage you are paying to accept Credit &amp; Debit Cards</em></p>
    <h1 class="headline" style="top:190px">No more %!??<span>Yes, it's true!</span></h1>

    <div class="pill">Pay&nbsp;<b>ZERO %</b>&nbsp;with Keystone Payments</div>

    <div class="offer__icon" style="top:325px"></div>
    <p class="offer__text" style="top:324px">We provide a free placed terminal or POS with a <strong>Minimal monthly service fee</strong></p>

    <div class="contact__tab">Contact our partner today and activate your savings</div>
    <div class="contact__box"></div>

    <p class="site">www.<span>keystonehq</span>.com</p>
  </article>

  <!-- Spanish side -->
  <article class="flyer flyer--es" lang="es">
    <svg class="chart" viewBox="0 0 499 180" aria-hidden="true">
      <g fill="#1e56b3">
        <rect x="20" y="110" width="6" height="70"/><rect x="40" y="90" width="6" height="90"/>
        <rect x="60" y="120" width="6" height="60"/><rect x="80" y="70" width="6" height="110"/>
        <rect x="100" y="100" width="6" height="80"/><rect x="120" y="60" width="6" height="120"/>
        <rect x="140" y="85" width="6" height="95"/><rect x="160" y="50" width="6" height="130"/>
        <rect x="180" y="95" width="6" height="85"/><rect x="200" y="40" width="6" height="140"/>
        <rect x="220" y="75" width="6" height="105"/><rect x="240" y="55" width="6" height="125"/>
        <rect x="260" y="80" width="6" height="100"/><rect x="280" y="45" width="6" height="135"/>
      </g>
      <polyline points="10,130 60,100 110,115 160,70 210,85 260,40 300,30" fill="none" stroke="#2a9df4" stroke-width="1.5"/>
    </svg>

    <div class="brand"><span class="brand__dot"></span><span class="brand__name">KEYSTONE</span></div>

    <div class="panel"></div>
    <p class="panel__kicker" style="top:94px">Keystone Payments toma la</p>
    <h2 class="panel__title" style="top:108px;font-size:17.5px;line-height:1.1">El dolor de Procesamiento de pagos</h2>
    <p class="panel__sub" style="top:175px;font-weight:700">¡Al entregarle una mayor parte de sus ganancias!</p>

    <div class="photo" role="img" aria-label="Compradora sonriente con tarjeta y bolsas junto a un terminal de pago y una bolsa de dinero"></div>

    <div class="seal">
      <small>Nos especializamos en</small>
      <p>Negocios latinos con personal de ventas y soporte en español</p>
    </div>

    <p class="intro" style="top:124px;width:215px">Cómo ahorrar miles por<em>Eliminando el porcentaje que estás pagando por aceptar Tarjetas de Crédito y Débito</em></p>
    <h1 class="headline" style="top:193px">¡No más %!??<span>¡Sí, es verdad!</span></h1>

    <div class="pill">¡Paga&nbsp;<b>CERO %</b>&nbsp;con Keystone Payments</div>

    <div class="offer__icon" style="top:328px"></div>
    <p class="offer__text" style="top:327px;width:135px">Ofrecemos un terminal o TPV gratuito con una <strong>tarifa de servicio mensual mínima.</strong></p>

    <div class="contact__tab">Contacte con nuestro socio hoy y active sus ahorros</div>
    <div class="contact__box"></div>

    <p class="site">www.<span>keystonehq</span>.com</p>
  </article>

</main>
</body>
</html>
```